Executive Business Card for Healthcare Company [Need Today]

I need a business card design for a healthcare company. The only branding the company has thus far is a logo. The cards will be utilized by company executives. The design I envision will be vibrant and appealing but with a corporate feel. They shouldn't be too casual or playful. I would like to complete this project TODAY if possible.

Target Market(s)

Healthcare vendors, other executives in healthcare and pharmaceuticals

Industry/Entity Type

Pharmaceutical

Contact Information for Business Card

See attachment

Font styles to use
Serif
Sans Serif

Colors

Designer to choose colors to be used in the design.

```html
<!DOCTYPE html>
<html lang="en">
<head>
<meta charset="utf-8">
<title>Corvane Health – Executive Business Card</title>
<link rel="stylesheet" href="https://fonts.googleapis.com/css2?family=Roboto:wght@300;400;500;700&display=swap">
<style>
  :root {
    --teal: #2fa89a;
    --teal-deep: #1f9aa8;
    --grey: #8a8a8a;
    --grey-dark: #555555;
    --stripe: #7d7d7d;
    --paper: #ffffff;
    --backdrop: #e4e4e4;
    --font: "Roboto", Arial, sans-serif;
  }
  * { margin: 0; padding: 0; box-sizing: border-box; }
  html, body { width: 1200px; height: 726px; overflow: hidden; }
  body {
    background: var(--backdrop);
    font-family: var(--font);
    position: relative;
  }
  .card {
    position: absolute;
    top: 208px;
    width: 540px;
    height: 309px;
    background: var(--paper);
    box-shadow: 0 2px 10px rgba(0,0,0,0.12);
    overflow: hidden;
  }
  .card--front { left: 40px; }
  .card--back { left: 620px; }

  .brand {
    position: absolute;
    display: flex;
    align-items: center;
    gap: 14px;
  }
  .brand__dot {
    width: 52px; height: 52px;
    border: 3px solid var(--teal);
    border-radius: 50%;
    flex: none;
  }
  .brand__name {
    font-family: var(--font);
    font-weight: 400;
    font-size: 30px;
    color: var(--teal-deep);
    letter-spacing: 0.5px;
    white-space: nowrap;
  }
  .card--front .brand { left: 50%; top: 108px; transform: translateX(-50%); }
  .card--back .brand { left: 70px; top: 62px; }
  .card--back .brand__dot { width: 46px; height: 46px; }
  .card--back .brand__name { font-size: 26px; }

  .website {
    position: absolute;
    left: 0; right: 0;
    top: 232px;
    text-align: center;
    font-size: 13px;
    letter-spacing: 3.5px;
    color: var(--grey-dark);
  }
  .website__domain { color: var(--teal-deep); }

  .holder { position: absolute; left: 36px; top: 196px; }
  .holder__name { font-size: 22px; font-weight: 500; color: var(--teal-deep); }
  .holder__title { font-size: 11px; color: var(--grey); margin-top: 3px; }

  .wave { position: absolute; inset: 0; }

  .contact {
    position: absolute;
    right: 20px;
    top: 136px;
    list-style: none;
    text-align: right;
    color: #ffffff;
    font-size: 12px;
    font-weight: 300;
    line-height: 19px;
  }
  .contact__item { display: flex; justify-content: flex-end; align-items: center; gap: 8px; }
  .contact__icon { width: 11px; height: 11px; flex: none; }
  .address {
    position: absolute;
    right: 20px;
    bottom: 50px;
    color: #ffffff;
    font-size: 12px;
    font-weight: 300;
  }
</style>
</head>
<body>
  <section class="card card--front" aria-label="Card front">
    <div class="brand">
      <span class="brand__dot"></span>
      <span class="brand__name">Corvane Health</span>
    </div>
    <p class="website">www.<span class="website__domain">corvanerx</span>.com</p>
  </section>

  <section class="card card--back" aria-label="Card back">
    <svg class="wave" viewBox="0 0 540 309" width="540" height="309" aria-hidden="true">
      <path fill="var(--stripe)" d="M140 300 C 250 292, 290 240, 314 162 C 342 82, 420 38, 540 28 L540 39 C 428 50, 355 90, 326 166 C 300 244, 262 296, 140 300 Z"/>
      <path fill="var(--teal)" d="M90 309 C 230 300, 290 250, 332 170 C 364 94, 436 56, 540 47 L540 309 Z"/>
    </svg>
    <div class="brand">
      <span class="brand__dot"></span>
      <span class="brand__name">Corvane Health</span>
    </div>
    <div class="holder">
      <p class="holder__name">Daniel Mercer</p>
      <p class="holder__title">Senior Director of Marketing</p>
    </div>
    <ul class="contact">
      <li class="contact__item">555-014-2290
        <svg class="contact__icon" viewBox="0 0 12 12"><path fill="#fff" d="M2 1h2l1 3-1.3 1a7 7 0 0 0 3.3 3.3L8 7l3 1v2a1 1 0 0 1-1 1A9 9 0 0 1 1 2a1 1 0 0 1 1-1z"/></svg>
      </li>
      <li class="contact__item">555-014-7716
        <svg class="contact__icon" viewBox="0 0 12 12"><rect x="3" y="0.5" width="6" height="11" rx="1" fill="none" stroke="#fff"/><circle cx="6" cy="9.5" r="0.8" fill="#fff"/></svg>
      </li>
      <li class="contact__item">dmercer@corvanerx.com
        <svg class="contact__icon" viewBox="0 0 12 12"><circle cx="6" cy="6" r="5" fill="none" stroke="#fff"/><ellipse cx="6" cy="6" rx="2.2" ry="5" fill="none" stroke="#fff"/><path d="M1 6h10" stroke="#fff"/></svg>
      </li>
    </ul>
    <p class="address">118 Linden Avenue Marlow, GA 30999</p>
  </section>
</body>
</html>
```